Classy, Elegant, Simple Business Card Design

Looking to have a classy, simple, and elegant design. Want a top notch designed business card. I really like the look of the new torvane credit card. I also like the design I attached. I am trying to reach 21-29 year old females for booking us for there wedding or event. We offer Disc Jockey Service, Photo Booth Rentals, and Uplighting .

Target Market(s)

21-28 year old females

Contact Information for Business Card

Has to have logo, website, email, and phone number

Font styles to use
Other font styles liked:
• open to font choice, modern, clean
Designer to choose
33a6d7
0791cd
0555a3
ffffff

Requirements
Must have
• Has to have logo, website, email, and phone number
Nice to have
• I really like the design of the new torvane credit card. I also included my logo and some designs I like
Should not have
• clutter or too much info

```html
<!DOCTYPE html>
<html lang="en">
<head>
<meta charset="utf-8">
<title>Tidemark Event Group – Business Card</title>
<link rel="stylesheet" href="https://fonts.googleapis.com/css2?family=Lato:wght@400;700&display=swap">
<style>
  :root {
    --navy: #12335e;
    --navy-deep: #0f2c52;
    --pattern-tone: #173b6b;
    --blue: #0791cd;
    --sky: #33a6d7;
    --royal: #0555a3;
    --paper: #f4f4f4;
    --ink: #2f3b4a;
    --rule: #c9cdd2;
    --backdrop: #dfe2e6;
  }
  * { margin: 0; padding: 0; box-sizing: border-box; }
  html, body {
    width: 1200px; height: 1015px; overflow: hidden;
    background: var(--backdrop);
    font-family: "Lato", sans-serif;
  }
  .canvas {
    position: relative; width: 1200px; height: 1015px;
  }
  .card {
    position: absolute; left: 180px; width: 840px; height: 480px;
    box-shadow: 0 10px 28px rgba(0,0,0,.18);
    overflow: hidden;
  }
  /* Back side */
  .card-back { top: 20px; background: var(--navy); }
  .card-back .pattern-field {
    position: absolute; inset: 0;
    background: radial-gradient(circle at 70% 40%, var(--pattern-tone), var(--navy-deep) 75%);
  }
  .card-back .back-mark {
    position: absolute; right: 120px; top: 170px;
    display: flex; align-items: center; gap: 12px;
    color: var(--sky); font-size: 30px; font-weight: 700; letter-spacing: 1px;
  }
  .mark-dot {
    width: 14px; height: 14px; border-radius: 50%; background: currentColor;
  }
  /* Front side */
  .card-front { top: 515px; background: var(--paper); }
  .brand-block {
    position: absolute; left: 60px; top: 150px; width: 330px;
    text-align: center;
  }
  .brand-name {
    display: flex; align-items: center; justify-content: center; gap: 12px;
    color: var(--blue); font-size: 38px; font-weight: 700; letter-spacing: 2px;
  }
  .brand-name .mark-dot { width: 16px; height: 16px; }
  .brand-sub {
    margin-top: 8px; color: #9aa3ad; font-size: 15px; letter-spacing: 7px;
  }
  .divider {
    position: absolute; left: 420px; top: 105px; width: 1px; height: 170px;
    background: var(--rule);
  }
  .contact-list {
    position: absolute; left: 460px; top: 118px; list-style: none;
  }
  .contact-list li {
    display: flex; align-items: center; gap: 12px;
    font-size: 24px; color: var(--ink); line-height: 1; margin-bottom: 16px;
  }
  .contact-icon { width: 26px; height: 26px; flex: none; }
  .service-band {
    position: absolute; left: 0; right: 0; bottom: 0; height: 100px;
    background: var(--navy);
    display: flex; align-items: center; justify-content: center;
    color: #fff; font-size: 23px; letter-spacing: .5px;
  }
  .service-band .sep { margin: 0 12px; opacity: .8; }
</style>
</head>
<body>
<main class="canvas">
  <section class="card card-back" aria-label="Card back">
    <div class="pattern-field" role="img" aria-label="Repeating faint monogram pattern in deep navy tones"></div>
    <div class="back-mark"><span class="mark-dot"></span>Tidemark</div>
  </section>

  <section class="card card-front" aria-label="Card front">
    <div class="brand-block">
      <div class="brand-name"><span class="mark-dot"></span>TIDEMARK</div>
      <div class="brand-sub">EVENT GROUP</div>
    </div>
    <div class="divider"></div>
    <ul class="contact-list">
      <li>
        <svg class="contact-icon" viewBox="0 0 26 26" aria-hidden="true">
          <circle cx="13" cy="13" r="13" fill="var(--blue)"/>
          <path d="M9 7.5l2.2 0 1 3-1.5 1.1a8 8 0 0 0 3.7 3.7l1.1-1.5 3 1v2.2c0 .8-.7 1.4-1.5 1.3A11 11 0 0 1 7.7 9c-.1-.8.5-1.5 1.3-1.5z" fill="#fff"/>
        </svg>
        044-987 654 321
      </li>
      <li>
        <svg class="contact-icon" viewBox="0 0 26 26" aria-hidden="true">
          <circle cx="13" cy="13" r="13" fill="var(--blue)"/>
          <rect x="7" y="8.5" width="12" height="9" rx="1" fill="#fff"/>
          <path d="M7.5 9l5.5 4.5L18.5 9" fill="none" stroke="var(--blue)" stroke-width="1.3"/>
        </svg>
        hello@tidemarkevents.com
      </li>
      <li>
        <svg class="contact-icon" viewBox="0 0 26 26" aria-hidden="true">
          <circle cx="13" cy="13" r="13" fill="var(--blue)"/>
          <circle cx="13" cy="13" r="6" fill="none" stroke="#fff" stroke-width="1.4"/>
          <ellipse cx="13" cy="13" rx="2.6" ry="6" fill="none" stroke="#fff" stroke-width="1.2"/>
          <line x1="7" y1="13" x2="19" y2="13" stroke="#fff" stroke-width="1.2"/>
        </svg>
        www.tidemarkevents.com
      </li>
    </ul>
    <div class="service-band">
      Disc Jockey Service<span class="sep">|</span>Photo Booth Rentals<span class="sep">|</span>Uplighting
    </div>
  </section>
</main>
</body>
</html>
```